Business Card for a New Zealand IT Startup

I need a business card for VELTA Holdings. We are a young startup based in New Zealand working in internet marketing and web development. The design should have some element connected to New Zealand, such as wave, koru or silver fern, just don't use a kiwi bird.

```html
<!DOCTYPE html>
<html lang="en">
<head>
<meta charset="utf-8">
<title>VELTA Holdings – Business Card</title>
<link rel="stylesheet" href="https://fonts.googleapis.com/css2?family=Jost:wght@400;500;600;700&display=swap">
<style>
  :root {
    --bg: #e9e6e1;
    --card: #ffffff;
    --blue: #1669b6;
    --blue-deep: #0f5aa3;
    --orange: #ee5a24;
    --orange-light: #f37a45;
    --ink: #4a4a4a;
    --rule: #d6d6d6;
  }
  * { margin: 0; padding: 0; box-sizing: border-box; }
  html, body { width: 1200px; height: 1040px; overflow: hidden; }
  body {
    background: var(--bg);
    font-family: "Jost", sans-serif;
    position: relative;
  }
  .card {
    position: absolute;
    left: 250px;
    width: 700px;
    height: 400px;
    background: var(--card);
    border-radius: 28px;
    overflow: hidden;
    box-shadow: 0 10px 26px rgba(0,0,0,0.18);
  }
  .card--front { top: 90px; }
  .card--back { top: 550px; }

  .card__bands { position: absolute; inset: 0; width: 100%; height: 100%; }

  .identity {
    position: absolute;
    left: 60px;
    top: 172px;
    width: 280px;
    text-align: right;
  }
  .identity__name {
    color: var(--blue);
    font-size: 32px;
    font-weight: 500;
    letter-spacing: 0.3px;
    line-height: 1;
    white-space: nowrap;
  }
  .identity__role {
    color: var(--orange);
    font-size: 20px;
    font-weight: 400;
    margin-top: 6px;
  }
  .divider {
    position: absolute;
    left: 362px;
    top: 110px;
    width: 1px;
    height: 150px;
    background: var(--rule);
  }
  .contact {
    position: absolute;
    left: 388px;
    top: 112px;
    color: var(--ink);
    font-size: 17px;
    line-height: 25px;
    list-style: none;
  }
  .contact__item { display: flex; align-items: center; gap: 8px; white-space: nowrap; }
  .contact__icon { width: 14px; height: 14px; flex: none; }

  .brand {
    position: absolute;
    inset: 0;
    display: flex;
    align-items: center;
    justify-content: center;
    gap: 18px;
  }
  .brand__dot {
    width: 30px;
    height: 30px;
    border-radius: 50%;
    background: var(--blue);
  }
  .brand__name {
    color: var(--blue);
    font-size: 52px;
    font-weight: 600;
    letter-spacing: 3px;
    white-space: nowrap;
  }
</style>
</head>
<body>

<section class="card card--front" aria-label="Business card front">
  <svg class="card__bands" viewBox="0 0 700 400" preserveAspectRatio="none" aria-hidden="true">
    <path d="M700 0 L700 95 C560 40 420 18 300 0 Z" fill="var(--orange)"/>
    <path d="M700 0 L700 40 C610 20 540 8 480 0 Z" fill="var(--orange-light)"/>
    <path d="M0 400 L0 310 C180 370 420 385 700 330 L700 355 C460 400 230 400 0 400 Z" fill="var(--blue)"/>
    <path d="M0 400 L0 340 C150 385 300 395 420 400 Z" fill="var(--blue-deep)"/>
  </svg>

  <div class="identity">
    <h1 class="identity__name">MARA QUINLAN</h1>
    <p class="identity__role">CEO/FOUNDER</p>
  </div>

  <div class="divider"></div>

  <ul class="contact">
    <li class="contact__item">214 Harbour Terrace</li>
    <li class="contact__item">Wellington, NZ 6011</li>
    <li class="contact__item">
      <svg class="contact__icon" viewBox="0 0 14 14"><path d="M3 1 L5 4 L4 5.5 C5 7.5 6.5 9 8.5 10 L10 9 L13 11 L11.5 13 C6 12.5 1.5 8 1 2.5 Z" fill="var(--blue)"/></svg>
      021 584 3907
    </li>
    <li class="contact__item">
      <svg class="contact__icon" viewBox="0 0 14 14"><rect x="1.5" y="2" width="11" height="10" rx="1" fill="none" stroke="var(--blue)" stroke-width="1.6"/></svg>
      04 739 2618
    </li>
    <li class="contact__item">
      <svg class="contact__icon" viewBox="0 0 14 14"><rect x="1" y="3" width="12" height="8" fill="var(--blue)"/><path d="M1 3 L7 8 L13 3" fill="none" stroke="#fff" stroke-width="1.2"/></svg>
      mara@veltaholdings.com
    </li>
    <li class="contact__item">
      <svg class="contact__icon" viewBox="0 0 14 14"><circle cx="7" cy="7" r="6" fill="var(--blue)"/><path d="M1 7 H13 M7 1 C4 4 4 10 7 13 M7 1 C10 4 10 10 7 13" fill="none" stroke="#fff" stroke-width="0.9"/></svg>
      www.veltaholdings.com
    </li>
  </ul>
</section>

<section class="card card--back" aria-label="Business card back">
  <div class="brand">
    <span class="brand__dot"></span>
    <span class="brand__name">VELTA HOLDINGS</span>
  </div>
</section>

</body>
</html>
```